Lumatrainer: an app for coaches and students in golf and fitness

I currently have an app that is called Lumatrainer and I am redoing the app completely and with this I am looking for a cool design for the app. I am not happy with the design as it is at the moment. The app should have a nice welcome and when you are logged in the dashboard must be very modern. It is a golf app that have 2 type of users. 1 user is the coach and the other user is the student. Those users can see different things of course.
The coach is normally paying a subscription charge for using the app but I want to get the students to pay for different tools that I will be offering via the app. To me the dashboard and the homepage of the app (once you have downloaded the app) is important. Here I would like to get the student as well as the coach the feeling of what the app can offer. The app offers features like Calendar (here the student can book the coach via the calendar), Chat (here the coach and the student can chat with each other as well as the coach can creat group chats with several students), Notes (here the coach as well as the student can create notes for their lessons), video tips (here the coach can upload video tips for his/her students, online lesson (the student can take online lessons by uploading recorded videos..and so on

Target Market(s)

Sport coaches (for start it will be mostly golf coaches)

Industry/Entity Type

Sports

Font styles to use
Sans Serif

Colors
0054AA
0677BA
7BADD7
CADEEF
E8F1F8

Requirements
Must have
• modern design and easy navigation.
Nice to have
• It all starts with the dashboard
Should not have
• boring standard style.

```html
<!DOCTYPE html>
<html lang="en">
<head>
<meta charset="utf-8">
<title>Lumatrainer – Messages</title>
<link rel="stylesheet" href="https://fonts.googleapis.com/css2?family=Poppins:wght@400;500;600&display=swap">
<style>
  :root {
    --brand: #0054AA;
    --brand-mid: #0677BA;
    --sky: #7BADD7;
    --mist: #CADEEF;
    --ice: #E8F1F8;
    --ink: #1d1d1f;
    --muted: #55575c;
    --field: #f5f6f8;
    --page: #eef4fa;
    --white: #ffffff;
    --fab-start: #12b8b0;
    --fab-end: #2a8fe6;
  }
  * { box-sizing: border-box; margin: 0; padding: 0; }
  html, body { width: 1200px; height: 864px; overflow: hidden; }
  body {
    background: var(--page);
    font-family: "Poppins", sans-serif;
    position: relative;
  }
  .screen {
    position: absolute;
    left: 450px; top: 107px;
    width: 300px; height: 650px;
    background: var(--brand);
    border-radius: 18px;
    overflow: hidden;
    box-shadow: 0 12px 40px rgba(0, 84, 170, 0.15);
  }
  .status-bar {
    position: absolute; left: 0; top: 0; width: 100%; height: 36px;
    color: var(--white);
  }
  .status-time {
    position: absolute; left: 26px; top: 9px;
    font-size: 12px; font-weight: 500;
  }
  .status-icons { position: absolute; right: 12px; top: 12px; }
  .app-bar {
    position: absolute; left: 10px; top: 40px;
    display: flex; align-items: center; gap: 10px;
    color: var(--white);
  }
  .app-bar h1 { font-size: 13px; font-weight: 500; letter-spacing: .1px; }
  .sheet {
    position: absolute; left: 0; top: 74px; width: 100%; bottom: 0;
    background: var(--white);
    border-radius: 16px 16px 0 0;
  }
  .search {
    position: absolute; left: 16px; top: 16px; width: 268px; height: 40px;
    background: var(--field); border-radius: 12px;
    display: flex; align-items: center; justify-content: space-between;
    padding: 0 12px 0 16px;
    font-size: 10.5px; color: #8a8c91;
  }
  .chat-row {
    position: absolute; left: 8px; width: 284px; height: 72px;
    border-radius: 10px;
  }
  .chat-row.is-active { background: var(--brand); }
  .avatar {
    position: absolute; left: 8px; top: 12px;
    width: 48px; height: 48px; border-radius: 50%;
  }
  .contact-name {
    position: absolute; left: 72px; top: 18px;
    font-size: 11.5px; font-weight: 500; color: var(--ink);
  }
  .preview {
    position: absolute; left: 72px; top: 38px;
    font-size: 9.5px; color: var(--muted);
    white-space: nowrap;
  }
  .stamp {
    position: absolute; right: 16px; top: 19px;
    font-size: 8.5px; color: var(--ink);
  }
  .unread-dot {
    position: absolute; right: 16px; top: 42px;
    width: 8px; height: 8px; border-radius: 50%; background: var(--brand);
  }
  .is-unread .contact-name, .is-unread .preview, .is-unread .stamp { color: var(--brand); }
  .is-unread .contact-name { font-weight: 600; }
  .is-active .contact-name, .is-active .preview, .is-active .stamp { color: var(--white); }
  .compose {
    position: absolute; left: 223px; top: 562px;
    width: 60px; height: 60px; border-radius: 50%;
    background: linear-gradient(135deg, var(--fab-start), var(--fab-end));
    display: flex; align-items: center; justify-content: center;
    box-shadow: 0 6px 16px rgba(6, 119, 186, .3);
  }
  .home-indicator {
    position: absolute; left: 97px; top: 638px;
    width: 106px; height: 3px; border-radius: 2px; background: #111;
  }
</style>
</head>
<body>
  <main class="screen">
    <div class="status-bar">
      <span class="status-time">9:41</span>
      <svg class="status-icons" width="54" height="10" viewBox="0 0 54 10" fill="#fff">
        <rect x="0" y="6" width="2.2" height="4" rx=".5"/>
        <rect x="3.5" y="4.5" width="2.2" height="5.5" rx=".5"/>
        <rect x="7" y="3" width="2.2" height="7" rx=".5"/>
        <rect x="10.5" y="1" width="2.2" height="9" rx=".5"/>
        <path d="M21 9.5 l-1.6-1.6a2.3 2.3 0 0 1 3.2 0z M17.6 6.2a4.8 4.8 0 0 1 6.8 0l-1 1a3.4 3.4 0 0 0-4.8 0z M15.6 4.2a7.6 7.6 0 0 1 10.8 0l-1 1a6.2 6.2 0 0 0-8.8 0z"/>
        <rect x="34" y="1" width="16" height="8" rx="2" fill="none" stroke="#fff" stroke-opacity=".5"/>
        <rect x="35.5" y="2.5" width="13" height="5" rx="1"/>
        <rect x="51" y="3.5" width="1.5" height="3" rx=".5" fill-opacity=".5"/>
      </svg>
    </div>

    <header class="app-bar">
      <svg width="16" height="16" viewBox="0 0 16 16" fill="none" stroke="#fff" stroke-width="1.6" stroke-linecap="round" stroke-linejoin="round">
        <path d="M14 8H2M7 3L2 8l5 5"/>
      </svg>
      <h1>Messages</h1>
    </header>

    <section class="sheet">
      <div class="search">
        <span>Search</span>
        <svg width="13" height="13" viewBox="0 0 14 14" fill="none" stroke="#0054AA" stroke-width="1.8" stroke-linecap="round">
          <circle cx="6" cy="6" r="4.6"/><path d="M9.5 9.5L12.6 12.6"/>
        </svg>
      </div>

      <div class="chat-row is-unread" style="top:71px">
        <div class="avatar" role="img" aria-label="Profile photo of Dorian Vale" style="background:linear-gradient(135deg,#3e5a3a,#a8643a)"></div>
        <span class="contact-name">Dorian Vale</span>
        <span class="preview">Sounds great! Thanks coach.</span>
        <span class="stamp">Friday</span>
        <span class="unread-dot"></span>
      </div>

      <div class="chat-row" style="top:143px">
        <div class="avatar" role="img" aria-label="Profile photo of Marisol Quinby" style="background:linear-gradient(135deg,#6f8a6a,#c9a491)"></div>
        <span class="contact-name">Marisol Quinby</span>
        <span class="preview">Okay. I’ll be there.</span>
        <span class="stamp">22 Apr</span>
      </div>

      <div class="chat-row is-active" style="top:217px">
        <div class="avatar" role="img" aria-label="Profile photo of Tobias Wrenfield" style="background:linear-gradient(135deg,#4b5a55,#b9a48a)"></div>
        <span class="contact-name">Tobias Wrenfield</span>
        <span class="preview">You: No problem</span>
        <span class="stamp">20 Apr</span>
      </div>

      <div class="chat-row is-unread" style="top:295px">
        <div class="avatar" role="img" aria-label="Profile photo of Elora Pembrook" style="background:linear-gradient(135deg,#5a86c4,#c8a17c)"></div>
        <span class="contact-name">Elora Pembrook</span>
        <span class="preview">Thanks!</span>
        <span class="stamp">19 Apr</span>
        <span class="unread-dot"></span>
      </div>

      <div class="chat-row" style="top:375px">
        <div class="avatar" role="img" aria-label="Profile photo of Callum Ashby" style="background:linear-gradient(135deg,#3f5e3c,#c59c7d)"></div>
        <span class="contact-name">Callum Ashby</span>
        <span class="preview">You: That’s good. Looking forward to...</span>
        <span class="stamp">18 Apr</span>
      </div>

      <div class="chat-row" style="top:455px">
        <div class="avatar" role="img" aria-label="Profile photo of Rowan Pike" style="background:linear-gradient(135deg,#8f9a8c,#7b5a47)"></div>
        <span class="contact-name">Rowan Pike</span>
        <span class="preview">You: No problem</span>
        <span class="stamp">16 Apr</span>
      </div>

      <div class="chat-row" style="top:528px">
        <div class="avatar" role="img" aria-label="Profile photo of Livia Moreno" style="background:linear-gradient(135deg,#d4b23a,#e6c3a8)"></div>
        <span class="contact-name">Livia Moreno</span>
        <span class="stamp">15 Apr</span>
      </div>
    </section>

    <div class="compose" aria-label="New message">
      <svg width="24" height="24" viewBox="0 0 24 24" fill="none" stroke="#fff" stroke-width="1.8" stroke-linecap="round" stroke-linejoin="round">
        <path d="M11 4H5a2 2 0 0 0-2 2v13a2 2 0 0 0 2 2h13a2 2 0 0 0 2-2v-6"/>
        <path d="M18.5 2.5a2.1 2.1 0 0 1 3 3L12 15l-4 1 1-4z"/>
      </svg>
    </div>

    <span class="home-indicator"></span>
  </main>
</body>
</html>
```